Duct Manufacturing Company new to the industry needs business card and stationary design

we are sheet metal duct manufacturers looking for a business card design to fit my new business logo.
nothing to crazy that will date, but want it to stand out from the crowed.
I'm sure you guys will work it out.

Contact Information for Business Card

Glen Marsh
Director

Address
17 Dorwell St
Tarrabool NSW 2631

0438 760 514

Sales@flowbend.com.au

Font styles to use
Other font styles liked:
• BankGothic md bt

Requirements
Nice to have
• Like the idea of corner rounded to match logo
• like to keep colours flowing
• font I like sharp square not rounded

```html
<!DOCTYPE html>
<html lang="en">
<head>
<meta charset="utf-8">
<title>Flowbend Industries – Business Card</title>
<link rel="stylesheet" href="https://fonts.googleapis.com/css2?family=Michroma&family=Montserrat:wght@400;500&display=swap">
<style>
  :root {
    --backdrop: #a3a2a3;
    --card-white: #fbfbfb;
    --panel-dark: #151618;
    --brand-green: #5db535;
    --brand-green-deep: #169a3c;
    --brand-blue: #1560b0;
    --brand-blue-light: #1d9ae0;
    --text-blue: #1b63ad;
    --text-grey: #444;
  }
  * { margin: 0; padding: 0; box-sizing: border-box; }
  html, body { width: 1200px; height: 1200px; overflow: hidden; }
  body {
    background: var(--backdrop);
    position: relative;
    font-family: "Montserrat", sans-serif;
  }
  .card {
    position: absolute;
    width: 712px;
    height: 419px;
    border-radius: 26px;
    overflow: hidden;
    background: var(--card-white);
  }
  .card--front { left: 238px; top: 118px; }
  .card--back { left: 230px; top: 643px; }
  .card svg { position: absolute; inset: 0; }

  .wordmark {
    position: absolute;
    left: 0; right: 0;
    text-align: center;
    font-family: "Michroma", sans-serif;
    line-height: 1.15;
  }
  .wordmark__dot {
    display: block;
    border-radius: 50%;
    margin: 0 auto;
    background: var(--brand-green);
  }
  .wordmark__name { display: block; letter-spacing: 1px; }
  .wordmark__sub { display: block; }

  .card--front .wordmark { top: 130px; color: var(--brand-blue); }
  .card--front .wordmark__dot { width: 60px; height: 60px; margin-bottom: 60px; }
  .card--front .wordmark__name { font-size: 34px; }
  .card--front .wordmark__sub { font-size: 26px; letter-spacing: 7px; }

  .card--back .wordmark {
    top: 155px; left: 0; width: 330px; right: auto;
    color: var(--brand-green);
  }
  .card--back .wordmark__dot { width: 50px; height: 50px; margin-bottom: 40px; }
  .card--back .wordmark__name { font-size: 31px; }
  .card--back .wordmark__sub { font-size: 22px; letter-spacing: 7.5px; }

  .contact {
    position: absolute;
    left: 398px;
    top: 76px;
    color: var(--text-grey);
  }
  .contact__name {
    font-family: "Michroma", sans-serif;
    color: var(--text-blue);
    font-size: 21px;
    letter-spacing: 1.5px;
    line-height: 1.2;
  }
  .contact__role { font-size: 16px; margin-top: 6px; }
  .contact__list { list-style: none; margin-top: 82px; }
  .contact__list li {
    display: flex; align-items: center;
    font-size: 19px; height: 27px;
  }
  .contact__list svg { position: static; width: 18px; height: 18px; margin-right: 18px; fill: var(--text-blue); }
  .contact__address { font-size: 18.5px; line-height: 23px; margin-top: 6px; }
</style>
</head>
<body>

<section class="card card--front">
  <svg width="712" height="419" viewBox="0 0 712 419" aria-hidden="true">
    <defs>
      <linearGradient id="band-green" x1="0" x2="1">
        <stop offset="0" stop-color="var(--brand-green-deep)"/>
        <stop offset="1" stop-color="var(--brand-green)"/>
      </linearGradient>
      <linearGradient id="band-blue" x1="0" x2="1">
        <stop offset="0" stop-color="var(--brand-blue-light)"/>
        <stop offset="1" stop-color="var(--brand-blue)"/>
      </linearGradient>
    </defs>
    <polygon points="0,401 503,401 465,419 0,419" fill="url(#band-green)"/>
    <polygon points="510,401 712,401 712,419 472,419" fill="url(#band-blue)"/>
  </svg>
  <div class="wordmark">
    <span class="wordmark__dot"></span>
    <span class="wordmark__name">FLOWBEND</span>
    <span class="wordmark__sub">INDUSTRIES</span>
  </div>
</section>

<section class="card card--back">
  <svg width="712" height="419" viewBox="0 0 712 419" aria-hidden="true">
    <defs>
      <linearGradient id="edge-blue" x1="0" y1="0" x2="0" y2="1">
        <stop offset="0" stop-color="var(--brand-blue-light)"/>
        <stop offset="1" stop-color="var(--brand-blue)"/>
      </linearGradient>
    </defs>
    <path d="M0 0 H334 C350 90 370 190 352 285 C342 340 330 385 318 419 H0 Z" fill="url(#edge-blue)"/>
    <path d="M0 0 H322 C338 90 356 190 338 285 C328 340 314 385 300 419 H0 Z" fill="var(--panel-dark)"/>
  </svg>
  <div class="wordmark">
    <span class="wordmark__dot"></span>
    <span class="wordmark__name">FLOWBEND</span>
    <span class="wordmark__sub">INDUSTRIES</span>
  </div>
  <div class="contact">
    <p class="contact__name">GLEN MARSH</p>
    <p class="contact__role">Director</p>
    <ul class="contact__list">
      <li><svg viewBox="0 0 24 24"><path d="M3 9c0-3 4-5 9-5s9 2 9 5v2h-5V8.5C14.5 8 9.5 8 8 8.5V11H3zM7 12h10l3 8H4z"/></svg>0438 760 514</li>
      <li><svg viewBox="0 0 24 24"><path fill-rule="evenodd" d="M12 2a10 10 0 1 0 0 20 10 10 0 0 0 0-20zm0 2c1.3 0 2.6 2.4 3 6H9c.4-3.6 1.7-6 3-6zM4.1 10h3c.1-2 .5-3.8 1.2-5A8 8 0 0 0 4.1 10zm0 4a8 8 0 0 0 4.2 5c-.7-1.2-1.1-3-1.2-5zm5 0c.3 3.6 1.6 6 2.9 6s2.6-2.4 3-6zm7.9 0c-.1 2-.5 3.8-1.2 5a8 8 0 0 0 4.1-5zm3-4a8 8 0 0 0-4.2-5c.7 1.2 1.1 3 1.2 5z"/></svg>flowbend.com.au</li>
      <li><svg viewBox="0 0 24 24"><path d="M2 5h20v14H2zm2 2v.5l8 6 8-6V7zm0 3v7h16v-7l-8 6z"/></svg>Sales@flowbend.com.au</li>
    </ul>
    <p class="contact__address">17 Dorwell St<br>Tarrabool NSW 2631</p>
  </div>
</section>

</body>
</html>
```